Logo for a Food & Beverage Franchise Company

We need a logo and stationary for a new company that just aquired a restaurant franchise. We need a sleep and professional logo with stationary.

Target Market(s)

Adults, resturaunt owners, franchisors (Companies who own food franchise companies such as Farrowbys Head Office, Toastwell International Franchise)
and Big Food and Beverage who wish to give franchise rights to us)

Industry/Entity Type

Restaurant

Logo Text

Velvet Harbor

Logo styles of interest
Emblem Logo
Pictorial/Combination Logo
Character Logo
Font styles to use
Serif
Sans Serif

Colors
ffc214
f78f20
f37022
faa54b
fece3e
fbed22

Requirements
Must have
• Maximum three color. The less the better.
Nice to have
• It does not have to have a crown, but if you wish to have a crown then it does not have to be so sharp and clear. Abstract is better.

```html
<!DOCTYPE html>
<html lang="en">
<head>
<meta charset="utf-8">
<title>Velvet Harbor Business Cards</title>
<link rel="stylesheet" href="https://fonts.googleapis.com/css2?family=Josefin+Sans:wght@600&family=PT+Sans:wght@700&display=swap">
<style>
  :root {
    --backdrop: #ececec;
    --card-charcoal: #3a3a3a;
    --brand-orange: #f79c00;
    --brand-white: #ffffff;
    --contact-grey: #d6d6d6;
  }
  * { margin: 0; padding: 0; box-sizing: border-box; }
  html, body { width: 1200px; height: 800px; overflow: hidden; }
  body {
    background: var(--backdrop);
    position: relative;
    font-family: "PT Sans", Arial, sans-serif;
  }
  .card {
    position: absolute;
    top: 257px;
    width: 500px;
    height: 286px;
    background: var(--card-charcoal);
    overflow: hidden;
    box-shadow: 0 6px 18px rgba(0,0,0,0.18);
  }
  .card--back { left: 50px; }
  .card--front { left: 650px; }

  .band {
    position: absolute;
    top: 0;
    height: 100%;
    background: var(--brand-orange);
  }
  .card--back .band { left: 175px; width: 150px; }
  .card--front .band { left: 50px; width: 70px; }

  .band-wordmark {
    position: absolute;
    top: 50%;
    left: 50%;
    transform: translate(-50%, -50%);
    font-family: "Josefin Sans", Arial, sans-serif;
    font-weight: 600;
    font-size: 30px;
    line-height: 1.1;
    letter-spacing: 4px;
    text-align: center;
    color: var(--brand-white);
    text-transform: uppercase;
  }
  .band-square {
    position: absolute;
    left: 50%;
    top: 50%;
    width: 18px;
    height: 18px;
    transform: translate(-50%, -50%);
    background: var(--brand-white);
  }

  .identity {
    position: absolute;
    left: 160px;
    top: 62px;
  }
  .wordmark {
    font-family: "Josefin Sans", Arial, sans-serif;
    font-weight: 600;
    font-size: 25px;
    letter-spacing: 6px;
    color: var(--brand-white);
    text-transform: uppercase;
  }
  .holder {
    margin-top: 8px;
    font-size: 17px;
    color: var(--brand-orange);
  }
  .contact {
    position: absolute;
    left: 160px;
    top: 168px;
    list-style: none;
    font-size: 14px;
    line-height: 20px;
    color: var(--contact-grey);
  }
  .contact .address { font-size: 16px; margin-top: 2px; }
</style>
</head>
<body>
  <section class="card card--back" aria-label="Business card back">
    <div class="band">
      <div class="band-wordmark">Velvet<br>Harbor</div>
    </div>
  </section>

  <section class="card card--front" aria-label="Business card front">
    <div class="band">
      <div class="band-square"></div>
    </div>
    <div class="identity">
      <div class="wordmark">Velvet Harbor</div>
      <div class="holder">Rashid Al Noor C.E.O.</div>
    </div>
    <ul class="contact">
      <li>Office: +9714 280 4410</li>
      <li>Mobile: +97150 617 2093</li>
      <li>Email: rashid@velvetharbor.com</li>
      <li class="address">P.O. Box 5832, Dubai, UAE</li>
    </ul>
  </section>
</body>
</html>
```